Varelko App for Smart Devices IoT WiFi Electronic

Varelko is a siren manufacturer. This application is used for the company's products that have a Wi-Fi connection and an internet connection, which can be configured and activated remotely through this application. In addition, this application is used to activate the siren at specific times for the start and end of shifts in companies and schools. Users will be siren installers and IT or HR managers.
In addition to activating motorized sirens timers, some siren models have speakers and allow you to play TTS (text to speech) audio, audio recorded by the user on the phone and upload audio (mp3) with playlist programming with start and end times.
Application screens: home with dashboard (one dashboard for each category). Device categories: timers, speakers, motorized siren. Screen for requesting evaluation in the Play Store. Screen for registering the user profile. Screen for registering devices according to their category (timers, speakers, motorized siren). Screen for registering device groups. Screen for pairing the device on the client's Wi-Fi network. Screen for registering activation times. Screen for uploading MP3 audios. Screen for registering playlists with audio selection, start and end times. Screen for recording audio for later sending to the speakers. Screen for converting text to speech and sending to the speakers. It is important to have a time picker with the day of the week to program the activation times and playlist.

Target Market(s)

Schools, Companies and Stores.

Industry/Entity Type

IoT

Font styles to use
Sans Serif
Other font styles liked:
• roboto

Colors
FFC000
F8CF3A
FAE287
FDF2CF
FEFAEE

Requirements
Must have
• time picker with weekdays for timer programming feature.
Nice to have
• app review request screen on play store

```html
<!DOCTYPE html>
<html lang="en">
<head>
<meta charset="utf-8">
<title>Varelko – Welcome</title>
<link rel="stylesheet" href="https://fonts.googleapis.com/css2?family=Comfortaa:wght@600&family=Roboto:wght@500;700&display=swap">
<style>
  :root {
    --amber: #FFC000;
    --amber-deep: #F0BE05;
    --gold: #F8CF3A;
    --butter: #FAE287;
    --cream: #FDF2CF;
    --ivory: #FEFAEE;
    --ink: #1D1D1F;
    --white: #FFFFFF;
  }
  * { margin: 0; padding: 0; box-sizing: border-box; }
  html, body { width: 1200px; height: 2181px; overflow: hidden; background: var(--white); }
  .welcome-screen {
    position: relative;
    width: 1200px;
    height: 2181px;
    overflow: hidden;
    background: linear-gradient(180deg, #F3D99A 0%, #F8DE8C 35%, #FBE187 60%, #FDDD7A 100%);
  }
  .status-bar {
    position: absolute;
    top: 0; left: 0; right: 0;
    height: 130px;
    display: flex;
    align-items: center;
    justify-content: space-between;
    padding: 0 70px 0 90px;
    font-family: "Roboto", sans-serif;
    font-weight: 700;
    font-size: 40px;
    color: var(--ink);
  }
  .status-icons { display: flex; gap: 16px; align-items: center; }
  .brand-name {
    position: absolute;
    top: 860px;
    left: 0; right: 0;
    text-align: center;
    font-family: "Comfortaa", sans-serif;
    font-weight: 600;
    font-size: 210px;
    letter-spacing: 2px;
    color: var(--ivory);
    opacity: 0.85;
  }
  .bottom-wave { position: absolute; left: 0; bottom: 0; width: 1200px; height: 2181px; }
  .start-button {
    position: absolute;
    left: 492px;
    top: 1674px;
    width: 216px;
    height: 216px;
    border-radius: 50%;
    background: var(--white);
    border: 0;
    display: flex;
    align-items: center;
    justify-content: center;
  }
</style>
</head>
<body>
  <main class="welcome-screen">
    <header class="status-bar">
      <span class="status-time">09:41</span>
      <span class="status-icons" aria-hidden="true">
        <svg width="44" height="30" viewBox="0 0 44 30"><rect x="0" y="20" width="8" height="10" rx="2" fill="#1D1D1F"/><rect x="12" y="14" width="8" height="16" rx="2" fill="#1D1D1F"/><rect x="24" y="8" width="8" height="22" rx="2" fill="#1D1D1F" opacity=".35"/><rect x="36" y="0" width="8" height="30" rx="2" fill="#1D1D1F" opacity=".35"/></svg>
        <svg width="42" height="30" viewBox="0 0 42 30"><path d="M21 28l6-7a9 9 0 0 0-12 0z" fill="#1D1D1F"/><path d="M9 15a17 17 0 0 1 24 0" stroke="#1D1D1F" stroke-width="5" fill="none" stroke-linecap="round"/><path d="M3 8a26 26 0 0 1 36 0" stroke="#1D1D1F" stroke-width="5" fill="none" stroke-linecap="round"/></svg>
        <svg width="62" height="30" viewBox="0 0 62 30"><rect x="1" y="3" width="53" height="24" rx="7" fill="none" stroke="#1D1D1F" stroke-width="2" opacity=".4"/><rect x="4" y="6" width="47" height="18" rx="4" fill="#1D1D1F"/><rect x="57" y="11" width="4" height="8" rx="2" fill="#1D1D1F" opacity=".4"/></svg>
      </span>
    </header>

    <h1 class="brand-name">Varelko</h1>

    <svg class="bottom-wave" viewBox="0 0 1200 2181" aria-hidden="true">
      <circle cx="600" cy="1782" r="175" fill="none" stroke="#F8CF3A" stroke-width="90" opacity=".45"/>
      <path d="M0 1880 C150 1760 350 1748 560 1770 C760 1792 950 1792 1200 1640 L1200 2181 L0 2181 Z" fill="var(--amber-deep)"/>
    </svg>

    <button class="start-button" aria-label="Get started">
      <svg width="70" height="70" viewBox="0 0 70 70" aria-hidden="true"><path d="M22 14 L50 35 L22 56" fill="none" stroke="var(--amber)" stroke-width="7" stroke-linecap="round" stroke-linejoin="round"/></svg>
    </button>
  </main>
</body>
</html>
```